Meridale Bed Company Needs Business Card

Looking for a very nice looking business card. Creative but not extravagant. We sell beds and pillows across the U.S. and need something professional but catchy. I have attached the logo.

Name : Devin Holt
Title : President
Phone : (800) 471-2960
Email: sleep@quilmora.com
Website: www.quilmora.com

Can be single-sided or double-sided
horizontal or vertical

Can use Blues/Greys

Target Market(s)

Mass Market

Industry/Entity Type

Retail

Contact Information for Business Card

Name : Devin Holt
Title : President
Phone : (800) 471-2960
Email: sleep@quilmora.com
Website: www.quilmora.com

Requirements
Must have
• Clean, Modern, Smooth
• Can use Blues/Greys
• On the other side without the information - have something simple like www.quilmora.com or our logo
Nice to have
• Surprise me
Should not have
• Nothing crazy, nothing cluttered

```html
<!DOCTYPE html>
<html lang="en">
<head>
<meta charset="utf-8">
<title>Meridale Bed Company — Business Card</title>
<link href="https://fonts.googleapis.com/css2?family=Open+Sans:wght@300;400;600&display=swap" rel="stylesheet">
<style>
  :root {
    --stage: #1a1a1a;
    --card: #ffffff;
    --brand-blue: #2a9fd8;
    --ink: #333333;
  }
  * { margin: 0; padding: 0; box-sizing: border-box; }
  html, body {
    width: 1200px;
    height: 900px;
    overflow: hidden;
    background: var(--stage);
    font-family: "Open Sans", Arial, sans-serif;
  }
  .canvas { position: relative; width: 1200px; height: 900px; }
  .card {
    position: absolute;
    top: 306px;
    width: 440px;
    height: 271px;
    background: var(--card);
    border-radius: 12px;
  }
  .card--front { left: 149px; }
  .card--back { left: 608px; }
  .wordmark {
    position: absolute;
    font-weight: 300;
    color: var(--brand-blue);
    letter-spacing: 1px;
    line-height: 1;
    white-space: nowrap;
  }
  .card--front .wordmark { left: 30px; top: 42px; font-size: 56px; }
  .card--back .wordmark {
    left: 0; right: 0; top: 104px;
    text-align: center;
    font-size: 60px;
  }
  .holder { position: absolute; left: 234px; top: 128px; }
  .holder__name {
    font-size: 15px;
    font-weight: 600;
    color: var(--brand-blue);
    line-height: 20px;
  }
  .holder__title { font-size: 12.5px; color: var(--ink); line-height: 16px; }
  .contact { position: absolute; left: 234px; top: 185px; list-style: none; }
  .contact__item {
    display: flex;
    align-items: center;
    gap: 7px;
    font-size: 12.5px;
    color: var(--ink);
    line-height: 16px;
  }
  .contact__icon { width: 10px; height: 10px; fill: var(--brand-blue); flex: none; }
</style>
</head>
<body>
<main class="canvas">
  <section class="card card--front" aria-label="Card front">
    <div class="wordmark">quilmora</div>
    <div class="holder">
      <p class="holder__name">Devin Holt</p>
      <p class="holder__title">President</p>
    </div>
    <ul class="contact">
      <li class="contact__item">
        <svg class="contact__icon" viewBox="0 0 10 10" aria-hidden="true"><path d="M2 0.5 L3.6 2.8 L2.8 3.8 Q3.8 5.9 6.2 7.2 L7.2 6.4 L9.5 8 L8.4 9.5 Q4.5 9.2 0.5 1.6 Z"/></svg>
        (800) 471-2960
      </li>
      <li class="contact__item">
        <svg class="contact__icon" viewBox="0 0 10 10" aria-hidden="true"><path d="M1 2.5 H9 V7.8 H1 Z M1.4 2.9 L5 5.6 L8.6 2.9" stroke="#fff" stroke-width="0.8"/></svg>
        sleep@quilmora.com
      </li>
      <li class="contact__item">
        <svg class="contact__icon" viewBox="0 0 10 10" aria-hidden="true"><circle cx="5" cy="5" r="4.5"/><path d="M2.5 3 Q4 2.5 4.5 4 Q3.5 5.5 5 6.5 Q4.5 8 3.5 8.5 M6 1.5 Q7 3 8.5 3.5" stroke="#fff" stroke-width="0.8" fill="none"/></svg>
        www.quilmora.com
      </li>
    </ul>
  </section>
  <section class="card card--back" aria-label="Card back">
    <div class="wordmark">quilmora</div>
  </section>
</main>
</body>
</html>
```